Business Card Design

We are a commercial real estate brokerage in San Francisco, leasing office buildings downtown.
I would like a clean, elegant look. Simple but powerful .

Industry/Entity Type

Business

Contact Information for Business Card

Derek Holloway
lic# 07258143
415.555.0172
derek@velt-commercial.example
velt-commercial.example

```html
<!DOCTYPE html>
<html lang="en">
<head>
<meta charset="utf-8">
<title>Velt Commercial – Business Card</title>
<link href="https://fonts.googleapis.com/css2?family=Lato:wght@400;700&display=swap" rel="stylesheet">
<style>
  :root {
    --stage: #3a322d;
    --card: #0d0d0f;
    --card-edge: #1a1a1d;
    --accent: #8d9bbb;
    --grey: #7f8083;
    --text: #e4e4e6;
    --rule: #5b6a8c;
  }
  * { margin: 0; padding: 0; box-sizing: border-box; }
  html, body {
    width: 1200px; height: 844px; overflow: hidden;
    background: var(--stage);
    font-family: "Lato", "Helvetica Neue", Arial, sans-serif;
  }
  .stage {
    position: relative; width: 1200px; height: 844px;
    display: flex; align-items: center; justify-content: center; gap: 60px;
  }
  .card {
    position: relative; width: 510px; height: 292px;
    background: var(--card);
    border: 1px solid var(--card-edge);
    box-shadow: 0 14px 30px rgba(0,0,0,.45);
    overflow: hidden;
  }
  .logo { display: flex; align-items: center; gap: 14px; }
  .logo-art {
    width: 118px; height: 72px;
    background: linear-gradient(180deg, #6f7276 0%, #3a3c40 70%, #26272a 100%);
  }
  .logo-divider { width: 1px; height: 72px; background: #3b3c40; }
  .logo-name {
    color: var(--accent); font-weight: 700;
    line-height: 1; text-transform: uppercase;
  }
  .logo-name .line1 { display: block; font-size: 44px; letter-spacing: 1px; }
  .logo-name .line2 { display: block; font-size: 17px; letter-spacing: 2.5px; margin-top: 3px; }

  /* back side with contact details */
  .card-back .logo { position: absolute; left: 72px; top: 58px; }
  .card-back .rule {
    position: absolute; left: 0; top: 160px; width: 318px; height: 1px;
    background: var(--rule);
  }
  .contact {
    position: absolute; right: 30px; top: 146px;
    text-align: right; color: var(--text); font-size: 13.5px; line-height: 1;
  }
  .contact .name { color: var(--accent); font-size: 17px; margin-bottom: 9px; }
  .contact .lic { color: var(--accent); font-size: 14px; margin-bottom: 20px; }
  .contact .lic b { color: var(--text); font-weight: 400; }
  .contact .row {
    display: flex; justify-content: flex-end; align-items: center;
    gap: 8px; margin-bottom: 10px;
  }
  .contact .row svg { width: 11px; height: 11px; fill: var(--accent); }

  /* front side with centred logo */
  .card-front { display: flex; align-items: center; justify-content: center; }
</style>
</head>
<body>
<main class="stage">
  <section class="card card-back">
    <div class="logo">
      <div class="logo-art" role="img" aria-label="Illustration of downtown office towers"></div>
      <div class="logo-divider"></div>
      <div class="logo-name"><span class="line1">Velt</span><span class="line2">Commercial</span></div>
    </div>
    <div class="rule"></div>
    <div class="contact">
      <p class="name">Derek Holloway</p>
      <p class="lic">Lic# <b>07258143</b></p>
      <p class="row">415.555.0172
        <svg viewBox="0 0 24 24"><path d="M6.6 10.8a15.1 15.1 0 0 0 6.6 6.6l2.2-2.2c.3-.3.7-.4 1-.2 1.1.4 2.3.6 3.6.6.6 0 1 .4 1 1V20c0 .6-.4 1-1 1A17 17 0 0 1 3 4c0-.6.4-1 1-1h3.5c.6 0 1 .4 1 1 0 1.3.2 2.5.6 3.6.1.3 0 .7-.2 1z"/></svg>
      </p>
      <p class="row">derek@velt-commercial.example
        <svg viewBox="0 0 24 24"><path d="M2 5h20v14H2z M3 6l9 7 9-7" fill="none" stroke="#8d9bbb" stroke-width="2.4"/></svg>
      </p>
      <p class="row">velt-commercial.example
        <svg viewBox="0 0 24 24"><path d="M10 14a4 4 0 0 0 5.7 0l3.5-3.5a4 4 0 0 0-5.7-5.7L12 6.3M14 10a4 4 0 0 0-5.7 0l-3.5 3.5a4 4 0 0 0 5.7 5.7l1.5-1.5" fill="none" stroke="#8d9bbb" stroke-width="2.4" stroke-linecap="round"/></svg>
      </p>
    </div>
  </section>

  <section class="card card-front">
    <div class="logo">
      <div class="logo-art" role="img" aria-label="Illustration of downtown office towers"></div>
      <div class="logo-divider"></div>
      <div class="logo-name"><span class="line1">Velt</span><span class="line2">Commercial</span></div>
    </div>
  </section>
</main>
</body>
</html>
```